Ward Compass Business Card Design*

We need a business card design for our company Ward Compass. Our company is specialized in providing online consulting services regarding medical institutions, hospitals and doctors. We work with patients worldwide looking to choose between healthcare providers. We have a website you may use as a reference, where we list doctors and clinics worldwide. So we target Medical providers as well as patients worldwide.
Target Market(s)
Medical Providers and patients around the world
Industry/Entity Type
Medical
Contact Information for Business Card
Salwa Kettani
CEO
+90 612 348 2175
info@wardcompass.example
www.wardcompass.example
14 Annakhil 7 H.R.B. Rabat, Morocco
Requirements
Must have
- Company logo/name on one full side, personal info and smaller logo and company name on the other side.
Nice to have
- Smart and elegant design

```html
<!DOCTYPE html>
<html lang="en">
<head>
<meta charset="utf-8">
<title>Ward Compass — Business Card</title>
<link rel="stylesheet" href="https://fonts.googleapis.com/css2?family=Montserrat:wght@400;700&family=Arimo:wght@400&display=swap">
<style>
  :root{
    --navy:#123a66;
    --navy-deep:#0f355c;
    --grey-text:#8a8a8c;
    --ink:#3b3b3d;
    --paper:#ffffff;
    --stage:#2a2a2c;
  }
  *{box-sizing:border-box;margin:0;padding:0}
  html,body{width:1200px;height:880px;overflow:hidden;background:var(--stage)}
  .canvas{position:relative;width:1200px;height:880px}
  .card{position:absolute;left:300px;width:600px;height:343px;border-radius:22px;overflow:hidden}
  .card--brand{top:58px;background:var(--navy-deep)}
  .card--contact{top:479px;background:var(--paper)}

  .wordmark{position:absolute;display:flex;align-items:center;gap:12px;
    font-family:"Montserrat",sans-serif;font-weight:700;letter-spacing:.02em;white-space:nowrap}
  .wordmark__dot{border-radius:50%;flex:none}
  .card--brand .wordmark{left:150px;top:150px;font-size:26px;color:var(--paper)}
  .card--brand .wordmark__dot{width:44px;height:44px;background:var(--paper)}

  .person{position:absolute;left:52px;top:104px;font-family:"Montserrat",sans-serif}
  .person__name{font-size:34px;letter-spacing:.01em;line-height:1}
  .person__first{font-weight:700;color:var(--navy)}
  .person__last{font-weight:400;color:var(--grey-text)}
  .person__role{display:block;text-align:right;font-size:15px;color:var(--navy);margin-top:4px}

  .contacts{position:absolute;left:52px;top:192px;list-style:none;
    font-family:"Arimo",sans-serif;font-size:14px;color:var(--ink)}
  .contacts li{display:flex;align-items:center;gap:10px;height:22px}
  .contacts svg{width:16px;height:16px;flex:none}

  .band{position:absolute;left:0;top:272px;width:330px;height:40px;background:var(--navy)}
  .card--contact .wordmark{left:336px;top:262px;gap:10px;font-size:17px;color:var(--navy)}
  .card--contact .wordmark__dot{width:50px;height:50px;background:var(--navy)}
</style>
</head>
<body>
<main class="canvas">
  <section class="card card--brand" aria-label="Card front">
    <div class="wordmark"><span class="wordmark__dot"></span>WARD COMPASS</div>
  </section>

  <section class="card card--contact" aria-label="Card back">
    <div class="person">
      <h1 class="person__name"><span class="person__first">SALWA</span> <span class="person__last">KETTANI</span></h1>
      <span class="person__role">CEO</span>
    </div>
    <ul class="contacts">
      <li>
        <svg viewBox="0 0 16 16" aria-hidden="true"><circle cx="8" cy="8" r="8" fill="#123a66"/><path d="M5.6 4.2l1.3 1.6-.7.9c.5 1.1 1.3 1.9 2.3 2.4l.9-.7 1.6 1.3-.6 1.3c-2.9-.3-5.2-2.6-5.5-5.5z" fill="#fff"/></svg>
        +90 612 348 2175
      </li>
      <li>
        <svg viewBox="0 0 16 16" aria-hidden="true"><circle cx="8" cy="8" r="8" fill="#123a66"/><rect x="4.2" y="5.3" width="7.6" height="5.4" fill="none" stroke="#fff" stroke-width="1"/><path d="M4.2 5.3L8 8.4l3.8-3.1" fill="none" stroke="#fff" stroke-width="1"/></svg>
        info@wardcompass.example
      </li>
      <li>
        <svg viewBox="0 0 16 16" aria-hidden="true"><circle cx="8" cy="8" r="8" fill="#123a66"/><circle cx="8" cy="8" r="4" fill="none" stroke="#fff" stroke-width=".9"/><ellipse cx="8" cy="8" rx="1.7" ry="4" fill="none" stroke="#fff" stroke-width=".9"/><path d="M4 8h8" stroke="#fff" stroke-width=".9"/></svg>
        www.wardcompass.example
      </li>
    </ul>
    <div class="band"></div>
    <div class="wordmark"><span class="wordmark__dot"></span>WARD COMPASS</div>
  </section>
</main>
</body>
</html>
```